Brightwater Care Partners, LLC Business Card update!

would like a classier business card. Our cards currently just have our logo and contact information. Need better use of color and creativity
Logo attached.

Target Market(s)

Potential clients, contacts, existing clients. We are a consulting company

Industry/Entity Type

Business

Contact Information for Business Card

We like our colors but just have a boring card with our logo and a white background. I want something that stands out.

Colors
ec1f27
757575

Requirements
Must have
• Color to stay consistent. Logo provided
Nice to have
• Just better use of color/ design

```html
<!DOCTYPE html>
<html lang="en">
<head>
<meta charset="utf-8">
<title>Brightwater Care Partners – Business Card</title>
<link href="https://fonts.googleapis.com/css2?family=Electrolize&display=swap" rel="stylesheet">
<style>
  :root {
    --brand-magenta: #d4116b;
    --brand-grey: #757575;
    --ink: #2b2b2b;
    --paper: #ffffff;
    --paper-shade: #e9e9ea;
    --backdrop: #c9ccd0;
  }
  * { margin: 0; padding: 0; box-sizing: border-box; }
  html, body {
    width: 1200px; height: 864px; overflow: hidden;
    background: var(--backdrop);
    font-family: "Electrolize", "Segoe UI", sans-serif;
  }
  .card {
    position: absolute; left: 75px; top: 132px;
    width: 1050px; height: 600px;
    overflow: hidden;
    background: var(--brand-magenta);
    box-shadow: 0 14px 40px rgba(0,0,0,.22);
  }
  .card__shapes { position: absolute; inset: 0; }
  .brand {
    position: absolute; right: 60px; top: 44px;
    display: flex; align-items: center; gap: 16px;
  }
  .brand__dot {
    width: 46px; height: 46px; border-radius: 50%;
    background: var(--brand-magenta);
  }
  .brand__name {
    font-size: 42px; line-height: 1; color: var(--brand-magenta);
    letter-spacing: .5px;
  }
  .contact {
    position: absolute; right: 60px; top: 138px;
    text-align: right; color: var(--ink);
    font-size: 22px; letter-spacing: 1px;
  }
  .contact__address { margin-bottom: 20px; line-height: 1.45; }
  .contact__row {
    display: flex; justify-content: flex-end; align-items: center;
    gap: 12px; height: 36px;
  }
  .contact__icon { width: 24px; height: 24px; fill: var(--brand-grey); }
  .person {
    position: absolute; left: 70px; bottom: 56px; color: var(--paper);
  }
  .person__name { font-size: 34px; letter-spacing: 2px; }
  .person__title { font-size: 22px; letter-spacing: 1px; margin-top: 6px; margin-left: 30px; }
</style>
</head>
<body>
  <main class="card">
    <svg class="card__shapes" viewBox="0 0 1050 600" width="1050" height="600" aria-hidden="true">
      <defs>
        <radialGradient id="paperGlow" cx="0.45" cy="0.55" r="0.7">
          <stop offset="0" stop-color="var(--paper)"/>
          <stop offset="1" stop-color="var(--paper-shade)"/>
        </radialGradient>
      </defs>
      <g transform="rotate(12 760 120)">
        <ellipse cx="734" cy="138" rx="640" ry="300" fill="var(--paper)"/>
        <ellipse cx="748" cy="128" rx="640" ry="300" fill="var(--brand-grey)"/>
        <ellipse cx="760" cy="120" rx="640" ry="300" fill="url(#paperGlow)"/>
      </g>
    </svg>

    <div class="brand">
      <span class="brand__dot"></span>
      <span class="brand__name">Brightwater Care Partners</span>
    </div>

    <section class="contact">
      <p class="contact__address">214 Harbour View,<br>Tidewater Lane BWC</p>
      <p class="contact__row">012 555 0147
        <svg class="contact__icon" viewBox="0 0 24 24"><path d="M6.6 10.8a15 15 0 0 0 6.6 6.6l2.2-2.2a1 1 0 0 1 1-.25 11.4 11.4 0 0 0 3.6.57 1 1 0 0 1 1 1V20a1 1 0 0 1-1 1A17 17 0 0 1 3 4a1 1 0 0 1 1-1h3.5a1 1 0 0 1 1 1c0 1.25.2 2.45.57 3.57a1 1 0 0 1-.25 1z"/></svg>
      </p>
      <p class="contact__row">012 555 0148
        <svg class="contact__icon" viewBox="0 0 24 24"><path d="M7 1h10a2 2 0 0 1 2 2v18a2 2 0 0 1-2 2H7a2 2 0 0 1-2-2V3a2 2 0 0 1 2-2zm0 3v14h10V4zm5 15.5a1.2 1.2 0 1 0 0 2.4 1.2 1.2 0 0 0 0-2.4z"/></svg>
      </p>
      <p class="contact__row">012 555 0149
        <svg class="contact__icon" viewBox="0 0 24 24"><path d="M6 2h9l3 3v5h1a2 2 0 0 1 2 2v9H3v-9a2 2 0 0 1 2-2h1zm2 2v6h8V6h-2V4zm0 10v2h2v-2zm4 0v2h2v-2zm4 0v2h2v-2z"/></svg>
      </p>
      <p class="contact__row">hello@brightwatercare.com
        <svg class="contact__icon" viewBox="0 0 24 24"><path d="M2 5h20v14H2zm2 2v.5l8 5 8-5V7zm0 2.9V17h16V9.9l-8 5z"/></svg>
      </p>
      <p class="contact__row">www.brightwatercare.com
        <svg class="contact__icon" viewBox="0 0 24 24"><path d="M12 2a10 10 0 1 0 0 20 10 10 0 0 0 0-20zm6.9 6h-2.9a15 15 0 0 0-1.4-3.6A8 8 0 0 1 18.9 8zM12 4c.8 1.1 1.5 2.5 1.9 4h-3.8c.4-1.5 1.1-2.9 1.9-4zM4.3 14a8 8 0 0 1 0-4h3.3a16 16 0 0 0 0 4zm.8 2h2.9c.3 1.3.8 2.5 1.4 3.6A8 8 0 0 1 5.1 16zM8 8H5.1a8 8 0 0 1 4.3-3.6C8.8 5.5 8.3 6.7 8 8zm4 12c-.8-1.1-1.5-2.5-1.9-4h3.8c-.4 1.5-1.1 2.9-1.9 4zm2.3-6H9.7a14 14 0 0 1 0-4h4.6a14 14 0 0 1 0 4zm.3 5.6c.6-1.1 1.1-2.3 1.4-3.6h2.9a8 8 0 0 1-4.3 3.6zm1.8-5.6a16 16 0 0 0 0-4h3.3a8 8 0 0 1 0 4z"/></svg>
      </p>
    </section>

    <div class="person">
      <p class="person__name">DANIEL WHITMORE</p>
      <p class="person__title">Managing Director</p>
    </div>
  </main>
</body>
</html>
```